Qvx Brightforge Website

All the descriptions are available in the attached file. The designer has to structure the website and find the right images and icons. The website should look modern and avoid using images of real humans rather use animated images. Please note that the design should include home page, all the 4 services page , the contact us would be at the bottom of home page.

```html
<!DOCTYPE html>
<html lang="en">
<head>
<meta charset="utf-8">
<title>Qvx Brightforge</title>
<link href="https://fonts.googleapis.com/css2?family=Poppins:wght@400;500;600;700&display=swap" rel="stylesheet">
<style>
:root{
  --blue:#0b6fd6;
  --orange:#f7a21b;
  --ink:#3a3a3a;
  --text:#555;
  --cream:#f8f5ec;
  --dark:#2e2e30;
  --white:#fff;
}
*{box-sizing:border-box;margin:0;padding:0}
html,body{width:1200px;height:4112px;overflow:hidden}
body{position:relative;font-family:'Poppins',sans-serif;background:var(--white);color:var(--text)}
.abs{position:absolute}
.brand{font-weight:600;font-size:24px;color:var(--blue);display:flex;align-items:center;gap:10px}
.brand-dot{width:18px;height:18px;border-radius:50%;background:var(--blue)}
.nav{top:52px;left:544px;display:flex;gap:0;font-size:13px;font-weight:500;color:var(--ink)}
.nav a{position:absolute;white-space:nowrap;text-decoration:none;color:inherit}
.btn-blue{left:946px;top:40px;width:142px;height:45px;background:var(--blue);color:#fff;font-size:13px;font-weight:600;display:flex;align-items:center;justify-content:center;border-radius:2px}
.hero{left:0;top:128px;width:1200px;height:600px;background:linear-gradient(100deg,#16c4e8 0%,#0b5fc4 35%,#0a2f86 65%,#081c5a 100%)}
.hero-art{left:60px;top:150px;width:560px;height:560px;background:radial-gradient(circle at 45% 50%,rgba(90,160,255,.45),rgba(10,40,120,0) 70%)}
.hero h1{left:654px;top:306px;font-size:47px;font-weight:600;color:#fff;letter-spacing:.5px}
.hero-text{left:654px;top:382px;width:436px;font-size:17px;line-height:27px;color:#fff;text-align:justify}
.btn-orange{background:var(--orange);color:#fff;font-size:13px;font-weight:600;display:flex;align-items:center;justify-content:center;border-radius:2px}
.about{left:0;top:728px;width:1200px;height:498px;background:var(--cream)}
.sec-title{font-size:38px;font-weight:600;color:var(--ink);white-space:nowrap}
.sec-title b{color:var(--blue);font-weight:600}
.about .sec-title{left:0;width:1200px;text-align:center;top:92px}
.about p{left:148px;top:172px;width:904px;text-align:center;font-size:16px;line-height:28px}
.btn-line{border:2px solid var(--orange);color:var(--ink);font-size:13px;font-weight:500;display:flex;align-items:center;justify-content:center;border-radius:2px;background:#fff}
.svc-title{font-size:34px;font-weight:600;color:var(--ink);white-space:nowrap}
.svc-title b{color:var(--blue);font-weight:600}
.svc-text{width:456px;font-size:16px;line-height:27.5px;text-align:justify}
.svc-icon{width:76px;height:76px;border-radius:50%;background:#fff;box-shadow:0 4px 16px rgba(0,0,0,.1);display:flex;align-items:center;justify-content:center}
.art{border-radius:8px}
.contact{left:0;top:3296px;width:1200px;height:816px;background:radial-gradient(ellipse at 50% 100%,#3c3c40 0%,var(--dark) 60%)}
.contact h2{left:0;width:1200px;top:62px;text-align:center;font-size:38px;font-weight:600;color:#fff}
.form{left:503px;top:155px;width:563px;height:335px;background:#eef2f8;border-radius:10px}
.field{background:#fff;border-radius:3px;font-size:13px;color:#777;padding:14px 18px}
.info{left:130px;display:flex;gap:28px;align-items:flex-start;color:#fff}
.info .ic{width:46px;height:46px;border-radius:50%;background:#fff;display:flex;align-items:center;justify-content:center;flex:none}
.info h4{font-size:14px;font-weight:600;margin-top:2px}
.info p{font-size:13px;line-height:24px}
.rule{left:112px;width:976px;height:1px;background:rgba(255,255,255,.25)}
.fnav{top:3966px;left:0;width:1200px;display:flex;justify-content:center;gap:22px;color:#fff;font-size:18px;font-weight:600}
.socials{top:4015px;left:0;width:1200px;display:flex;justify-content:center;gap:8px}
.socials span{width:26px;height:26px;border-radius:50%;border:2px solid #fff}
.socials span:first-child{background:var(--blue);border-color:var(--blue)}
.copy{top:4062px;left:0;width:1200px;text-align:center;font-size:12px;color:#fff}
</style>
</head>
<body>

<header>
  <div class="abs brand" style="left:115px;top:45px"><span class="brand-dot"></span>Qvx Brightforge</div>
  <nav class="abs nav">
    <a style="left:0;color:var(--orange)">HOME</a>
    <a style="left:82px">SERVICES</a>
    <a style="left:187px">PRODUCTS</a>
    <a style="left:305px">BLOG</a>
  </nav>
  <div class="abs btn-blue">CONTACT US</div>
</header>

<section class="abs hero">
  <div class="abs hero-art" style="top:0;left:0;width:660px;height:600px;background:radial-gradient(circle at 45% 50%,rgba(120,190,255,.35),rgba(10,40,120,0) 70%)" role="img" aria-label="Illustration of a laptop surrounded by web design, HTML, CSS and JS interface elements"></div>
</section>
<h1 class="abs hero" style="background:none;height:auto;left:654px;top:306px;width:auto;font-size:47px;font-weight:600;color:#fff">QVX BRIGHTFORGE</h1>
<p class="abs hero-text">Empower your digital journey with our advanced IT solutions. From data to web and mobile apps, we've got you covered.</p>
<div class="abs btn-orange" style="left:654px;top:493px;width:142px;height:46px">GET STARTED</div>

<section class="abs about">
  <h2 class="abs sec-title"><b>ABOUT</b> US</h2>
  <p class="abs">We are a forward-thinking IT consulting firm specializing in providing cutting-edge data analytics, web application development, and mobile app development services. Our passion for innovation and technology drives us to deliver tailor-made solutions that empower businesses to thrive in the digital landscape. We take pride in our ability to collaborate with early-stage startups as their technology partner, helping them navigate the challenges of launching and scaling their ventures.</p>
  <div class="abs btn-line" style="left:530px;top:349px;width:140px;height:47px">READ MORE</div>
</section>

<!-- Data analytics -->
<div class="abs art" style="left:108px;top:1388px;width:467px;height:304px;background:linear-gradient(135deg,#e6f0fb,#cfe2f6)" role="img" aria-label="Illustration of a dashboard screen with a magnifying glass and megaphone"></div>
<div class="abs svc-icon" style="left:632px;top:1341px"><svg width="34" height="34" viewBox="0 0 34 34"><circle cx="15" cy="15" r="9" fill="none" stroke="#f7a21b" stroke-width="3"/><line x1="22" y1="22" x2="30" y2="30" stroke="#f7a21b" stroke-width="4" stroke-linecap="round"/></svg></div>
<h3 class="abs svc-title" style="left:630px;top:1434px"><b>DATA</b> ANALYTICS</h3>
<p class="abs svc-text" style="left:632px;top:1498px">At Qvx Brightforge, our proficiency consists of linking your leadership team's objectives with the relevant data that holds significance. We recognize the importance of not only delivering precise and dependable data but also presenting it in a format that is easily comprehensible and aligned with your business goals.</p>
<div class="abs btn-line" style="left:634px;top:1695px;width:140px;height:44px">READ MORE</div>

<!-- Web development -->
<div class="abs svc-icon" style="left:110px;top:1823px"><svg width="34" height="34" viewBox="0 0 34 34"><rect x="3" y="5" width="28" height="24" rx="3" fill="#f7a21b"/><path d="M13 13l-4 4 4 4M21 13l4 4-4 4" fill="none" stroke="#fff" stroke-width="2.5"/></svg></div>
<h3 class="abs svc-title" style="left:108px;top:1914px"><b>WEB</b> DEVELOPMENT</h3>
<p class="abs svc-text" style="left:112px;top:1979px">At Qvx Brightforge, we are a trailblazing web development company committed to delivering cutting-edge digital solutions that empower businesses to excel in the ever-evolving online landscape. Our team of seasoned professionals combines technical prowess with a passion for innovation, transforming ideas</p>
<div class="abs btn-line" style="left:112px;top:2174px;width:140px;height:44px">READ MORE</div>
<div class="abs art" style="left:613px;top:1883px;width:472px;height:295px;background:linear-gradient(135deg,#fbf5e2,#e8ecfb)" role="img" aria-label="Illustration of a team building a website on a large browser window"></div>

<!-- Mobile app -->
<div class="abs art" style="left:108px;top:2362px;width:476px;height:322px;background:linear-gradient(135deg,#eef3fc,#dbe6f8)" role="img" aria-label="Illustration of a developer working at a desk with code windows"></div>
<div class="abs svc-icon" style="left:632px;top:2302px"><svg width="34" height="34" viewBox="0 0 34 34"><rect x="10" y="3" width="16" height="28" rx="3" fill="#f7a21b"/><rect x="13" y="7" width="10" height="18" fill="#fff"/></svg></div>
<h3 class="abs svc-title" style="left:630px;top:2396px"><b>MOBILE APP</b> DEVELOPMENT</h3>
<p class="abs svc-text" style="left:632px;top:2459px">At Qvx Brightforge, we are a pioneering mobile app development company dedicated to crafting exceptional digital experiences that captivate and engage users across various platforms. Our team of expert developers and designers combines passion, innovation, and technical mastery to transform</p>
<div class="abs btn-line" style="left:634px;top:2654px;width:140px;height:45px">READ MORE</div>

<!-- Start-up -->
<div class="abs svc-icon" style="left:110px;top:2782px"><svg width="34" height="34" viewBox="0 0 34 34"><circle cx="17" cy="17" r="13" fill="#f7a21b"/><circle cx="17" cy="17" r="5" fill="#fff"/></svg></div>
<h3 class="abs svc-title" style="left:108px;top:2875px"><b>START-UP</b> TECH PARTNER</h3>
<p class="abs svc-text" style="left:112px;top:2940px">At Qvx Brightforge, we are committed to supporting early-stage start-ups on their journey to success by providing comprehensive technical partner services. Our team of industry veterans collaborates with entrepreneurs to refine their ideas, develop minimum viable products (MVPs), strategize market entry</p>
<div class="abs btn-line" style="left:112px;top:3135px;width:140px;height:44px">READ MORE</div>
<div class="abs art" style="left:567px;top:2753px;width:582px;height:455px;background:linear-gradient(135deg,#f4f7fc,#e2ecf9)" role="img" aria-label="Illustration of business partners with gears and laptops"></div>

<!-- Contact -->
<section class="abs contact">
  <h2 class="abs">CONTACT US</h2>
  <div class="abs info" style="top:221px">
    <span class="ic"><svg width="20" height="20" viewBox="0 0 20 20"><path d="M10 1a6 6 0 0 0-6 6c0 5 6 12 6 12s6-7 6-12a6 6 0 0 0-6-6z" fill="var(--blue)"/><circle cx="10" cy="7" r="2.2" fill="#fff"/></svg></span>
    <div><h4>LOCATIONS:</h4><p>Suite 12/40 Harbourline Road,<br>Kestrel Bay WA 6190</p></div>
  </div>
  <div class="abs info" style="top:310px;align-items:center">
    <span class="ic"><svg width="20" height="20" viewBox="0 0 20 20"><path d="M5 2l3 4-2 2c1 2 3 4 5 5l2-2 4 3-2 3C8 17 3 12 2 5z" fill="var(--blue)"/></svg></span>
    <div><h4>PHONE:</h4><p>+61 (08) 5550 2417</p></div>
  </div>
  <div class="abs info" style="top:382px;align-items:center">
    <span class="ic"><svg width="20" height="20" viewBox="0 0 20 20"><rect x="2" y="4" width="16" height="12" rx="2" fill="var(--blue)"/><path d="M3 5l7 6 7-6" fill="none" stroke="#fff" stroke-width="1.5"/></svg></span>
    <div><h4>EMAIL:</h4><p>hello@qvxbrightforge.example</p></div>
  </div>

  <div class="abs form">
    <div class="abs field" style="left:28px;top:30px;width:248px;height:46px">First Name</div>
    <div class="abs field" style="left:285px;top:30px;width:249px;height:46px">Last Name</div>
    <div class="abs field" style="left:28px;top:90px;width:248px;height:47px">Email</div>
    <div class="abs field" style="left:285px;top:90px;width:249px;height:47px">Phone</div>
    <div class="abs field" style="left:28px;top:150px;width:506px;height:91px">Message</div>
    <div class="abs btn-orange" style="left:215px;top:256px;width:131px;height:45px;font-size:15px">SUBMIT</div>
  </div>

  <div class="abs rule" style="top:546px"></div>
  <div class="abs brand" style="left:0;width:1200px;justify-content:center;top:596px;color:#fff"><span class="brand-dot" style="background:#fff"></span>Qvx Brightforge</div>
</section>
<nav class="abs fnav"><span>HOME</span><span>/</span><span>SERVICES</span><span>/</span><span>PRODUCTS</span><span>/</span><span>BLOG</span><span>/</span><span>CONTACT US</span></nav>
<div class="abs socials"><span></span><span></span><span></span><span></span></div>
<div class="abs rule" style="top:4049px"></div>
<div class="abs copy">© 2023 Qvx Brightforge &nbsp;|&nbsp; All Rights Reserved</div>

</body>
</html>
```